Australian Trucking Company Requires Professional Looking Stationary

We require a professional looking stationary design that incorporates our newly designed logo.

Our business, called "Brell Haulage Contracting", provides contracting work, transport and logistics to business in Western Australia particularly with links to the mining sector.

We are a small business looking to expand and our new logo and our new stationary will help develop our brand image in our market place.

Target Market(s)

Businesses and Corporation with links to the Mining Sector

Industry/Entity Type

Small Business

Requirements
Must have
• The letterhead must have the following details:
The new logo

Text saying: "Brell Holdings Pty Ltd (ACN 582 316 907) ATF The Brell Discretionary Trust T/AS"
"ABN 71 834 209 553"
Address "P.O Box 817 Wattlegrove WA, 6958"
Phone: 08 9352 7140
Email: brellhaul@mailbox-example.com.au

The text on the letterhead should be editable as the details are likely to change in the near future. Provision should be made for a website address all though one isn't available at the moment.

The styling, layout and font text is entirely up to the designer.

```html
<!DOCTYPE html>
<html lang="en">
<head>
<meta charset="utf-8">
<title>Brell Haulage Contracting – Business Card</title>
<link href="https://fonts.googleapis.com/css2?family=Arimo:wght@400;700&display=swap" rel="stylesheet">
<style>
  :root{
    --page:#e9e6e2;
    --card:#ffffff;
    --red:#9b1b1e;
    --red-bright:#d41f26;
    --red-deep:#6e0b0e;
    --ink:#333333;
    --grey:#5f5f5f;
    --muted:#7a7a7a;
    --line:#1f2326;
  }
  *{margin:0;padding:0;box-sizing:border-box}
  html,body{width:1200px;height:1200px;overflow:hidden}
  body{background:var(--page);position:relative;font-family:"Arimo",Arial,sans-serif;color:var(--ink)}
  .card{position:absolute;width:840px;height:480px;background:var(--card);overflow:hidden;box-shadow:0 4px 14px rgba(0,0,0,.18)}
  .card--front{left:83px;top:80px}
  .card--back{left:284px;top:650px}
  .swoosh{position:absolute;left:0;top:0;width:840px;height:480px}
  .brand-mark{position:absolute;left:88px;top:70px;width:120px;height:120px;border-radius:50%;background:var(--grey)}
  .brand-name{position:absolute;left:274px;top:62px;font-weight:700;font-size:52px;line-height:54px;color:var(--red);text-transform:uppercase;letter-spacing:1px}
  .person{position:absolute;left:274px;top:244px;white-space:nowrap;color:var(--red)}
  .person__name{font-weight:700;font-size:32px}
  .person__sep{font-weight:700;font-size:30px;margin:0 14px 0 26px}
  .person__title{font-size:24px;letter-spacing:2px}
  .contacts{position:absolute;left:274px;top:316px;list-style:none}
  .contacts li{display:flex;align-items:center;height:35px;font-size:23px;white-space:nowrap}
  .contacts svg{width:18px;height:18px;margin-right:12px;fill:var(--red)}
  .back-mark{position:absolute;left:350px;top:40px;width:140px;height:140px;border-radius:50%;background:var(--grey)}
  .back-name{position:absolute;left:0;width:840px;top:208px;text-align:center;font-weight:700;font-size:34px;color:var(--grey);text-transform:uppercase;letter-spacing:1px}
  .web{position:absolute;left:0;width:840px;top:372px;text-align:center;font-size:32px;letter-spacing:3px;color:var(--ink)}
  .web b{color:var(--red);font-weight:700}
  .legal{position:absolute;left:0;width:840px;top:428px;text-align:center;font-size:19px;color:var(--muted);white-space:nowrap}
</style>
</head>
<body>

<section class="card card--front">
  <svg class="swoosh" viewBox="0 0 840 480" aria-hidden="true">
    <defs>
      <linearGradient id="redTop" x1="0" x2="1" y1="0" y2="0">
        <stop offset="0" stop-color="#ffffff"/>
        <stop offset=".45" stop-color="var(--red-bright)"/>
        <stop offset="1" stop-color="var(--red-deep)"/>
      </linearGradient>
      <linearGradient id="redBottom" x1="0" x2="1" y1="0" y2="0">
        <stop offset="0" stop-color="var(--red-deep)"/>
        <stop offset=".55" stop-color="var(--red-bright)"/>
        <stop offset="1" stop-color="#ffffff"/>
      </linearGradient>
    </defs>
    <path d="M480 0 Q700 20 840 124 L840 0 Z" fill="url(#redTop)"/>
    <path d="M480 0 Q700 20 840 124" fill="none" stroke="var(--line)" stroke-width="3"/>
    <path d="M0 352 Q160 460 360 480 L0 480 Z" fill="url(#redBottom)"/>
    <path d="M0 352 Q160 460 360 480" fill="none" stroke="var(--line)" stroke-width="3"/>
  </svg>

  <div class="brand-mark" aria-hidden="true"></div>
  <h1 class="brand-name">Brell<br>Haulage<br>Contracting</h1>

  <p class="person"><span class="person__name">Your Name</span><span class="person__sep">/</span><span class="person__title">Title</span></p>

  <ul class="contacts">
    <li><svg viewBox="0 0 24 24"><path d="M6.6 10.8a15 15 0 0 0 6.6 6.6l2.2-2.2a1 1 0 0 1 1-.25 11.4 11.4 0 0 0 3.6.57 1 1 0 0 1 1 1V20a1 1 0 0 1-1 1A17 17 0 0 1 3 4a1 1 0 0 1 1-1h3.5a1 1 0 0 1 1 1c0 1.25.2 2.45.57 3.57a1 1 0 0 1-.25 1z"/></svg>08 9352 7140</li>
    <li><svg viewBox="0 0 24 24"><path d="M2 5h20v3l-10 6L2 8z M2 10l10 6 10-6v9H2z"/></svg>brellhaul@mailbox-example.com.au</li>
    <li><svg viewBox="0 0 24 24"><path d="M12 2a10 10 0 1 0 0 20 10 10 0 0 0 0-20zm0 2c.9 0 2.1 1.8 2.6 5H9.4C9.9 5.8 11.1 4 12 4zM4.3 9h3.1a17 17 0 0 0 0 6H4.3a8 8 0 0 1 0-6zm5.1 0h5.2a15 15 0 0 1 0 6H9.4a15 15 0 0 1 0-6zm7.2 0h3.1a8 8 0 0 1 0 6h-3.1a17 17 0 0 0 0-6zM9.4 17h5.2c-.5 3.2-1.7 5-2.6 5s-2.1-1.8-2.6-5z"/></svg>www.brellhaulage.com</li>
    <li><svg viewBox="0 0 24 24"><path d="M12 3 2 12h3v9h5v-6h4v6h5v-9h3z"/></svg>P.O Box 817 Wattlegrove WA, 6958</li>
  </ul>
</section>

<section class="card card--back">
  <div class="back-mark" aria-hidden="true"></div>
  <p class="back-name">Brell Haulage Contracting</p>
  <p class="web">www.<b>brellhaulage</b>.com</p>
  <p class="legal">Brell Holdings Pty Ltd (ACN 582 316 907) ATF The Brell Discretionary Trust T/AS</p>
</section>

</body>
</html>
```